Accountability Project Graphics

I want to create 10 social media graphics (new Instagram size 4:5 (1080 x 1350 pixels) focusing on our Quilvo Accountability App, using any of the 3 pictures attached. Use the attached pics only, NO RANDOM STOCK PHOTOGRAPHY. For the color scheme, use the landing page colors/fonts (attached).
You can add any of the 3 photos attached but I mainly need BOLD text that includes these headlines and sub-headlines on them.
Please NOTE for all the headlines below, also add this sub-headline on each graphic:
Stay Consistent with RT in Your Pocket!
Here are the headlines:
• Stop Starting Over Every Monday
• You don't need more willpower. You need more support
• Built for women who are tired of doing this alone
• When Motivation Fades, RT Checks In
• The Support System You've Been Missing
• Support When Motivation Disappears
• What if RT Checked in Every Day?
• The Missing Piece Isn't Another Diet
• Eat the food you love. Stay accountable every day.
• One Bad Meal Doesn't Mean You Failed
women over 40 trying to lose weight

```html
<!DOCTYPE html>
<html lang="en">
<head>
<meta charset="utf-8">
<title>Accountability Graphics – Quilvo</title>
<link href="https://fonts.googleapis.com/css2?family=Crimson+Pro:wght@700&family=Alfa+Slab+One&family=Playfair+Display:wght@900&family=Montserrat:wght@500;600;700&display=swap" rel="stylesheet">
<style>
  :root{
    --navy:#2b1d3e;
    --rose:#c85a7c;
    --blush:#fbe4eb;
    --blush-soft:#f9eef2;
    --plum:#3e2244;
    --plum-light:#a9507a;
    --candy:#f5d3e0;
    --white:#ffffff;
    --photo-dark:#1f2638;
  }
  *{margin:0;padding:0;box-sizing:border-box}
  html,body{width:1200px;height:984px;overflow:hidden;background:var(--white)}
  .board{position:relative;width:1200px;height:984px}
  .post{position:absolute;width:337px;height:421px;overflow:hidden}
  .post--willpower{left:46px;top:46px;background:linear-gradient(160deg,#fdf1f4 0%,var(--blush) 55%,#e9b3c5 100%);border-top:2px solid var(--navy)}
  .post--bad-meal{left:430px;top:46px;background:linear-gradient(200deg,#f4c9d7 0%,#fbeef2 45%,var(--white) 75%)}
  .post--alone{left:813px;top:46px;background:var(--blush-soft)}
  .post--willpower-dark{left:46px;top:512px;background:linear-gradient(180deg,var(--plum) 0%,#6b3158 50%,var(--plum-light) 100%)}
  .post--check-in{left:430px;top:512px;background:var(--candy);border-top:3px solid var(--rose)}

  .abs{position:absolute}
  .photo{position:absolute;background:linear-gradient(180deg,#2a2f44 0%,var(--photo-dark) 60%,#161b2a 100%);border-radius:60px 60px 0 0}

  .head-serif{font-family:"Crimson Pro",Georgia,serif;font-weight:700;color:var(--navy)}
  .head-slab{font-family:"Alfa Slab One",Georgia,serif;font-weight:400;color:var(--navy)}
  .head-display{font-family:"Playfair Display",Georgia,serif;font-weight:900}
  .body-sans{font-family:"Montserrat",Arial,sans-serif}
  .pink{color:var(--rose)}

  .sub{font-family:"Montserrat",Arial,sans-serif;font-weight:500;color:var(--navy)}
  .rule{position:absolute;height:2px;background:var(--navy)}
  .divider{position:absolute;display:flex;align-items:center;gap:4px}
  .divider span{display:block;height:2px;background:var(--navy)}
  .divider i{display:block;width:3px;height:3px;background:var(--rose)}
</style>
</head>
<body>
<main class="board">

  <section class="post post--willpower">
    <svg class="abs" style="left:0;top:351px" width="337" height="70" viewBox="0 0 337 70">
      <path d="M0 0 H270 Q337 0 337 60 V70 H0 Z" fill="var(--rose)"/>
    </svg>
    <div class="photo" role="img" aria-label="Smiling coach in black lace top and jeans, hand on hip" style="left:205px;top:36px;width:132px;height:385px"></div>
    <h2 class="abs head-serif" style="left:22px;top:14px;font-size:37px;line-height:37px">You don't<br>Need More<br>Willpower.</h2>
    <p class="abs head-serif pink" style="left:22px;top:146px;font-size:37px;line-height:37px">You Need<br>More<br>Support</p>
    <div class="rule" style="left:22px;top:280px;width:90px"></div>
    <p class="abs sub" style="left:22px;top:293px;font-size:14px;line-height:19px">Stay Consistent with<br>RT in Your Pocket!</p>
  </section>

  <section class="post post--bad-meal">
    <svg class="abs" style="left:0;top:0" width="337" height="421" viewBox="0 0 337 421">
      <polygon points="0,0 337,0 337,10 0,66" fill="var(--rose)"/>
      <rect x="0" y="393" width="337" height="28" fill="var(--navy)"/>
    </svg>
    <div class="photo" role="img" aria-label="Coach in white with denim jacket laughing with a friend in a denim dress" style="left:135px;top:137px;width:202px;height:284px;background:linear-gradient(90deg,#2c3a5e 0%,#e8e8ea 35%,#2f4a72 70%,#3b5582 100%)"></div>
    <h2 class="abs head-serif" style="left:15px;top:76px;font-size:38px;line-height:36px">One Bad<br>Meal</h2>
    <p class="abs body-sans pink" style="left:16px;top:160px;font-size:25px;line-height:35px;font-weight:700">Doesn't<br>Mean<br>You<br>Failed</p>
    <div class="divider" style="left:16px;top:304px"><span style="width:22px"></span><i></i><span style="width:22px"></span></div>
    <p class="abs sub" style="left:15px;top:319px;font-size:12px;line-height:16px">Stay Consistent<br>with RT in Your<br>Pocket!</p>
  </section>

  <section class="post post--alone">
    <svg class="abs" style="left:0;top:0" width="337" height="421" viewBox="0 0 337 421">
      <polygon points="146,0 276,0 337,105 337,330 210,421 190,421" fill="var(--rose)"/>
      <polygon points="337,330 337,421 276,421" fill="var(--navy)"/>
    </svg>
    <div class="photo" role="img" aria-label="Smiling coach in black lace top and jeans, hand on hip" style="left:190px;top:20px;width:137px;height:401px"></div>
    <h2 class="abs head-slab" style="left:18px;top:58px;font-size:30px;line-height:38.5px">Built For<br>Women<br>Who Are<br>Tired of</h2>
    <p class="abs body-sans pink" style="left:18px;top:222px;font-size:26px;line-height:31px;font-weight:700">Doing This<br>Alone</p>
    <div class="divider" style="left:19px;top:293px"><span style="width:22px"></span><i></i><span style="width:22px"></span></div>
    <p class="abs sub" style="left:19px;top:316px;font-size:15.5px;line-height:22px">Stay Consistent<br>with RT in Your<br>Pocket!</p>
  </section>

  <section class="post post--willpower-dark">
    <div class="photo" role="img" aria-label="Smiling coach in black lace top and jeans, hand on hip" style="left:195px;top:18px;width:142px;height:403px"></div>
    <h2 class="abs head-slab" style="left:18px;top:56px;font-size:28px;line-height:37px;color:var(--white)">You Don't<br>Need More<br>Willpower.</h2>
    <p class="abs body-sans" style="left:19px;top:174px;font-size:26px;line-height:34px;font-weight:600;color:var(--white)">YOU NEED<br>MORE<br>SUPPORT</p>
    <div class="divider" style="left:19px;top:285px"><span style="width:22px;background:var(--white)"></span><i style="background:var(--white)"></i><span style="width:22px;background:var(--white)"></span></div>
    <p class="abs body-sans" style="left:19px;top:302px;font-size:15.5px;line-height:22px;font-weight:500;color:var(--white)">Stay Consistent<br>with RT in Your<br>Pocket!</p>
  </section>

  <section class="post post--check-in">
    <h2 class="abs head-display" style="left:0;top:16px;width:337px;text-align:center;font-size:28px;line-height:32px;color:var(--navy)">What if RT Checked in<br><span class="pink">Every Day?</span></h2>
    <div class="divider" style="left:119px;top:96px"><span style="width:40px"></span><i></i><span style="width:40px"></span></div>
    <p class="abs body-sans pink" style="left:0;top:113px;width:337px;text-align:center;font-size:15.5px;line-height:19px;font-weight:500">Stay Consistent with RT in<br>Your Pocket!</p>
    <div class="abs" role="img" aria-label="Coach in pink top hugging a smiling woman with curly hair" style="left:0;top:163px;width:337px;height:258px;background:radial-gradient(ellipse at 55% 55%,#c03c82 0%,#d9a3b8 45%,rgba(245,211,224,0) 75%)"></div>
  </section>

</main>
</body>
</html>
```